Graphic Design Project

Brinley-Cote Publications needs a graphic design for a new product called the "KORV Guide". We develop reference field guides for the construction industry and need the "KORV Guide" design to be worthy of its uniqueness.
The design can be in any color combination but must have a watermark or creative design to go with the name. We are getting ready to head start our 2012 volumes and need a new look.
Please do not add anything that looks like construction. We want a powerful look that is creative in nature with a new twist.
Please do not add Brinley-Cote Publications into the design since we already have a logo. Please stay true to "KORV Guide" and knock our socks off.
You always do.
Reason: I did not receive as many designs as I would have expected. I responded to all designers with feedback but was handicapped with the absence of attendees who had accepted my project. I submitted a written concern to Pixel Harbor a few days ago with no response.
Please help me by increasing my deadline to ensure I receive the design I so critically need to move my business forward successfully.
Thank you.
Graphic Design

```html
<!DOCTYPE html>
<html lang="en">
<head>
<meta charset="utf-8">
<title>KORV Guide – Volume Covers</title>
<link rel="stylesheet" href="https://fonts.googleapis.com/css2?family=Archivo+Black&display=swap">
<style>
  :root {
    --page-bg: #ffffff;
    --ink-light: #ffffff;

    --demo-hex: #f7961f;
    --demo-hex-edge: #ffb656;
    --demo-photo-dark: #2a1705;
    --demo-photo-mid: #6b3a0c;
    --demo-photo-light: #a3601a;
    --demo-tag: #f9a33a;
    --demo-word: rgba(214, 128, 34, 0.85);

    --steel-hex: #b40000;
    --steel-hex-edge: #d23030;
    --steel-photo-dark: #2e0000;
    --steel-photo-mid: #5e0000;
    --steel-photo-light: #8d0a0a;
    --steel-tag: #c41010;
    --steel-word: rgba(160, 0, 0, 0.9);
  }

  * { margin: 0; padding: 0; box-sizing: border-box; }

  html, body {
    width: 1200px;
    height: 840px;
    overflow: hidden;
    background: var(--page-bg);
  }

  .cover {
    position: absolute;
    top: 15px;
    width: 550px;
    height: 785px;
    overflow: hidden;
    box-shadow: 3px 3px 7px rgba(0, 0, 0, 0.45);
    font-family: "Archivo Black", "Arial Black", sans-serif;
    color: var(--ink-light);
  }
  .cover--demolition { left: 27px; }
  .cover--steel { left: 606px; }

  .cover__photo {
    position: absolute;
    inset: 0;
  }
  .cover--demolition .cover__photo {
    background:
      radial-gradient(ellipse at 78% 35%, var(--demo-photo-light) 0%, transparent 55%),
      linear-gradient(180deg, var(--demo-photo-mid) 0%, var(--demo-photo-dark) 60%, var(--demo-photo-mid) 100%);
  }
  .cover--steel .cover__photo {
    background:
      radial-gradient(ellipse at 70% 30%, var(--steel-photo-light) 0%, transparent 60%),
      linear-gradient(180deg, var(--steel-photo-mid) 0%, var(--steel-photo-dark) 55%, var(--steel-photo-mid) 100%);
  }

  .cover__hexes {
    position: absolute;
    inset: 0;
    width: 550px;
    height: 785px;
    filter: drop-shadow(4px 5px 4px rgba(0, 0, 0, 0.55));
  }
  .cover--demolition .cover__hexes { fill: var(--demo-hex); stroke: var(--demo-hex-edge); }
  .cover--steel .cover__hexes { fill: var(--steel-hex); stroke: var(--steel-hex-edge); }

  .cover__title {
    position: absolute;
    top: 6px;
    right: 145px;
    font-size: 28px;
    letter-spacing: -1.2px;
    line-height: 34px;
    white-space: nowrap;
  }

  .cover__volume {
    position: absolute;
    top: 0;
    right: 0;
    width: 130px;
    height: 30px;
    display: flex;
    align-items: center;
    justify-content: center;
    gap: 6px;
    font-size: 17px;
    letter-spacing: -0.5px;
  }
  .cover--demolition .cover__volume { background: var(--demo-tag); }
  .cover--steel .cover__volume { background: var(--steel-tag); }
  .cover__volume-number {
    border-left: 2px solid var(--ink-light);
    padding-left: 5px;
    line-height: 20px;
  }

  .cover__mark {
    position: absolute;
    top: 372px;
    right: 30px;
    text-align: right;
    line-height: 1;
  }
  .cover__mark-name {
    display: block;
    font-size: 108px;
    letter-spacing: -6px;
  }
  .cover__mark-sub {
    display: block;
    font-size: 40px;
    letter-spacing: -1.5px;
    margin-top: -6px;
    margin-right: 8px;
  }

  .cover__backdrop-word {
    position: absolute;
    left: -2px;
    bottom: -16px;
    font-size: 98px;
    letter-spacing: -6px;
    line-height: 1;
    white-space: nowrap;
  }
  .cover--demolition .cover__backdrop-word { color: var(--demo-word); }
  .cover--steel .cover__backdrop-word { color: var(--steel-word); font-size: 90px; }
</style>
</head>
<body>

<svg width="0" height="0" style="position:absolute" aria-hidden="true">
  <defs>
    <symbol id="hex" viewBox="0 0 200 173.2">
      <polygon points="2,86.6 51,1.5 149,1.5 198,86.6 149,171.7 51,171.7" stroke-width="3"/>
    </symbol>
  </defs>
</svg>

<article class="cover cover--demolition">
  <div class="cover__photo" role="img" aria-label="Toned photograph of a multi-storey building under demolition"></div>
  <svg class="cover__hexes" viewBox="0 0 550 785" aria-hidden="true">
    <use href="#hex" x="-33" y="-22.5" width="156" height="135"/>
    <use href="#hex" x="99" y="60.5" width="156" height="135"/>
    <use href="#hex" x="-33" y="130.5" width="156" height="135"/>
    <use href="#hex" x="227" y="130.5" width="156" height="135"/>
    <use href="#hex" x="357" y="68" width="134" height="116"/>
    <use href="#hex" x="98" y="206.5" width="156" height="135"/>
    <use href="#hex" x="163" y="280.5" width="438" height="379"/>
    <use href="#hex" x="47" y="481" width="136" height="118"/>
    <use href="#hex" x="-72" y="549" width="140" height="121"/>
    <use href="#hex" x="47" y="611" width="136" height="118"/>
  </svg>
  <h2 class="cover__title">Demolition</h2>
  <div class="cover__volume"><span>Volume</span><span class="cover__volume-number">6</span></div>
  <div class="cover__mark">
    <span class="cover__mark-name">KORV</span>
    <span class="cover__mark-sub">Guide</span>
  </div>
  <div class="cover__backdrop-word" aria-hidden="true">Demolition</div>
</article>

<article class="cover cover--steel">
  <div class="cover__photo" role="img" aria-label="Toned photograph of a steel frame structure with cranes"></div>
  <svg class="cover__hexes" viewBox="0 0 550 785" aria-hidden="true">
    <use href="#hex" x="-33" y="-22.5" width="156" height="135"/>
    <use href="#hex" x="99" y="60.5" width="156" height="135"/>
    <use href="#hex" x="-33" y="130.5" width="156" height="135"/>
    <use href="#hex" x="227" y="130.5" width="156" height="135"/>
    <use href="#hex" x="357" y="68" width="134" height="116"/>
    <use href="#hex" x="98" y="206.5" width="156" height="135"/>
    <use href="#hex" x="163" y="280.5" width="438" height="379"/>
    <use href="#hex" x="47" y="481" width="136" height="118"/>
    <use href="#hex" x="-72" y="549" width="140" height="121"/>
    <use href="#hex" x="47" y="611" width="136" height="118"/>
  </svg>
  <h2 class="cover__title">Steel Erection</h2>
  <div class="cover__volume"><span>Volume</span><span class="cover__volume-number">4</span></div>
  <div class="cover__mark">
    <span class="cover__mark-name">KORV</span>
    <span class="cover__mark-sub">Guide</span>
  </div>
  <div class="cover__backdrop-word" aria-hidden="true">Steel Erection</div>
</article>

</body>
</html>
```